Quiet Porch Podcast Cover Graphic

We need a graphic designed for a new podcast called "Quiet Porch." The graphic will be used on multiple podcasting platforms as the lead graphic advertising the podcast. The podcast consists of interviews of individuals sharing their life experiences including challenges, successes, lessons learned, and unexpected turns. The purpose of the podcast is to help listeners and participants learn from the life experiences of everyday neighbors. This podcast has a heavy Christian foundation on the parable of the good samaritan. We believe that through hearing the experiences of everyday neighbors, listeners can be strengthened, nourished, and aided to handle their own life challenges and trials. We would like the final design to be simple and reflective of the purpose and the parable of the good samaritan. The final design needs to have the title of the podcast, "Quiet Porch." We believe the best designs will limit the number of colors to less than 5 and will look good in a monochromatic version as well as a color version. We think the color white should be the main color. The graphic should be square in dimensions. We have considered having two hands grasping each other as if to lift the hand from below, but open to other creative simple takes to convey the lessons from the good samaritan.

```html
<!DOCTYPE html>
<html lang="en">
<head>
<meta charset="utf-8">
<title>Quiet Porch — Podcast Cover</title>
<link href="https://fonts.googleapis.com/css2?family=Oswald:wght@600&family=Yellowtail&display=swap" rel="stylesheet">
<style>
  :root {
    --stage: #333333;
    --paper: #f7f8f9;
    --paper-shade: #e9ecef;
    --frame-line: #3a3d42;
    --frame-soft: #9aa0a6;
    --bubble: #8fd0f2;
    --bubble-deep: #5fb6e6;
    --title-top: #8cc4ea;
    --title-bottom: #0f4f8a;
    --script: #1d6fb8;
    --skin-light: #cfcac0;
    --skin-dark: #7d786e;
  }
  * { margin: 0; padding: 0; box-sizing: border-box; }
  html, body {
    width: 767px; height: 1200px; overflow: hidden;
    background: var(--stage);
  }
  .cover {
    position: absolute; left: 40px; top: 256px;
    width: 687px; height: 687px; overflow: hidden;
    background: linear-gradient(160deg, var(--paper) 0%, #ffffff 55%, var(--paper-shade) 100%);
  }
  .cover-art { position: absolute; inset: 0; width: 687px; height: 687px; }
  .title { position: absolute; left: 0; right: 0; top: 0; height: 687px; }
  .title-main {
    position: absolute; left: 0; right: 0; top: 528px;
    text-align: center;
    font-family: "Oswald", "Arial Narrow", sans-serif;
    font-weight: 600; font-size: 158px; line-height: 1;
    letter-spacing: -2px;
    transform: scaleX(0.78) ;
    background: linear-gradient(180deg, var(--title-top) 0%, #2f7fc0 45%, var(--title-bottom) 100%);
    -webkit-background-clip: text; background-clip: text;
    color: transparent;
  }
  .title-script {
    position: absolute; left: 150px; top: 430px;
    font-family: "Yellowtail", cursive;
    font-size: 150px; line-height: 1;
    color: var(--script);
    transform: rotate(-8deg);
    text-shadow: 0 0 2px #ffffff, 0 0 4px #ffffff;
  }
</style>
</head>
<body>
  <main class="cover">
    <svg class="cover-art" viewBox="0 0 687 687" xmlns="http://www.w3.org/2000/svg">
      <defs>
        <linearGradient id="arm-tone" x1="0" y1="0" x2="1" y2="1">
          <stop offset="0" stop-color="var(--skin-light)"/>
          <stop offset="0.55" stop-color="#a39e94"/>
          <stop offset="1" stop-color="var(--skin-light)"/>
        </linearGradient>
      </defs>

      <g class="frame-lines" fill="none" stroke="var(--frame-line)" stroke-width="2">
        <path d="M170 29 H595 V292"/>
        <path d="M190 41 H575 V250"/>
        <path d="M240 55 H635 V320"/>
      </g>
      <g class="frame-verticals" stroke="var(--frame-soft)" stroke-width="2">
        <line x1="55" y1="185" x2="55" y2="600"/>
        <line x1="91" y1="200" x2="91" y2="640"/>
        <line x1="112" y1="170" x2="112" y2="560"/>
      </g>

      <g class="bubbles" fill="var(--bubble)" fill-opacity="0.55" stroke="var(--bubble-deep)" stroke-opacity="0.5">
        <path fill-rule="evenodd" d="M343 60 a225 225 0 1 0 0.1 0 Z M343 170 a115 115 0 1 1 -0.1 0 Z"/>
        <circle cx="300" cy="300" r="170" fill-opacity="0.25"/>
        <circle cx="431" cy="86" r="44"/>
        <circle cx="492" cy="122" r="17"/>
        <circle cx="175" cy="445" r="42"/>
        <circle cx="134" cy="390" r="11"/>
      </g>

      <polygon class="hands-photo" role="img"
        aria-label="Black-and-white photo of two hands clasping each other's wrists, one lifting the other"
        points="0,0 140,0 360,120 687,390 687,560 600,545 480,470 0,170"
        fill="url(#arm-tone)"/>
    </svg>

    <div class="title">
      <div class="title-main">PORCH</div>
      <div class="title-script">Quiet</div>
    </div>
  </main>
</body>
</html>
```